Consulting company business cards

We have a base design, but would be willing to update. We have a new logo/"tag" that needs to be added. Current business card design is attached for reference into our "style."

Industry/Entity Type

Business

Contact Information for Business Card

Should contain name and title, office number, mobile number if appropriate, e-mail, website, physical address, and company logo.

Font styles to use
Other font styles liked:
• See current card design on KorvandBCard

Colors
0455a3
85acd3
aaaaaa

Requirements
Must have
• Our colors are navy blue, gray, and a lighter blue
Nice to have
• Design that I can easily drop in new names/titles as we hire employees.

```html
<!DOCTYPE html>
<html lang="en">
<head>
<meta charset="utf-8">
<title>Harlow Business Cards</title>
<link href="https://fonts.googleapis.com/css2?family=Lato:wght@400;700;900&display=swap" rel="stylesheet">
<style>
  :root {
    --navy: #0b3a5e;
    --navy-deep: #08304f;
    --brand-blue: #0455a3;
    --light-blue: #85acd3;
    --gray: #aaaaaa;
    --ink: #3c4a58;
    --card-white: #f7f8fa;
    --stage: #1a1a1a;
  }
  * { margin: 0; padding: 0; box-sizing: border-box; }
  html, body { width: 1200px; height: 873px; overflow: hidden; }
  body {
    background: var(--stage);
    font-family: "Lato", Arial, sans-serif;
    position: relative;
  }
  .card {
    position: absolute;
    width: 540px;
    height: 310px;
    border-radius: 16px;
    overflow: hidden;
  }

  /* Front */
  .card-front { left: 60px; top: 110px; background: var(--card-white); color: var(--ink); }
  .map-area {
    position: absolute; left: 150px; top: 40px; width: 330px; height: 190px;
    background: radial-gradient(ellipse at center, #e3e9f1 0%, #edf1f6 60%, rgba(247,248,250,0) 100%);
  }
  .brand { position: absolute; left: 34px; top: 40px; display: flex; align-items: center; gap: 10px; }
  .brand-name { font-weight: 900; font-size: 46px; letter-spacing: 2px; color: var(--navy); line-height: 1; }
  .brand-dot { width: 26px; height: 26px; border-radius: 50%; background: var(--brand-blue); }
  .tagline {
    position: absolute; left: 36px; top: 92px;
    font-size: 11px; letter-spacing: 2.2px; text-transform: uppercase; color: var(--gray);
  }
  .person { position: absolute; right: 34px; top: 44px; text-align: right; }
  .person-name { font-size: 21px; color: var(--navy); }
  .person-name strong { font-weight: 700; }
  .person-title { font-size: 11px; color: var(--ink); margin-top: 2px; }
  .rule { position: absolute; left: 34px; right: 34px; top: 178px; height: 1px; background: #5c6a78; }
  .contact { position: absolute; left: 34px; top: 192px; list-style: none; font-size: 14px; color: var(--ink); }
  .contact li { display: flex; align-items: center; gap: 10px; height: 21px; }
  .contact svg { width: 13px; height: 13px; fill: var(--navy); }
  .contact .address { font-weight: 700; color: var(--navy); margin-top: 4px; }

  /* Back */
  .card-back { left: 620px; top: 450px; background: var(--navy); }
  .mark-circle {
    position: absolute; right: 40px; top: 40px; width: 150px; height: 150px;
    border-radius: 50%; background: #e9edf1;
  }
  .back-name {
    position: absolute; left: 40px; top: 186px;
    font-weight: 900; font-size: 62px; letter-spacing: 3px; color: #e9edf1; line-height: 1;
  }
  .back-url {
    position: absolute; left: 42px; top: 262px;
    font-size: 15px; letter-spacing: 4px; color: #dfe6ec;
  }
</style>
</head>
<body>
  <section class="card card-front">
    <div class="map-area" role="img" aria-label="Faint dotted world map background"></div>
    <div class="brand">
      <span class="brand-name">HARLOW</span>
      <span class="brand-dot"></span>
    </div>
    <p class="tagline">A Cloud Consulting Company</p>
    <div class="person">
      <p class="person-name">Dana <strong>Korvand</strong></p>
      <p class="person-title">Office Manager</p>
    </div>
    <div class="rule"></div>
    <ul class="contact">
      <li>
        <svg viewBox="0 0 16 16" aria-hidden="true"><path d="M3 1h3l1.5 4-2 1.2a9 9 0 0 0 4.3 4.3l1.2-2 4 1.5v3c0 1-1 2-2 2A13 13 0 0 1 1 3c0-1 1-2 2-2z"/></svg>
        555.014.2910
      </li>
      <li>
        <svg viewBox="0 0 16 16" aria-hidden="true"><path d="M4 1h8v4H4zM1 6h14v7h-3v2H4v-2H1zm4 4v4h6v-4z"/></svg>
        555.014.2971
      </li>
      <li>
        <svg viewBox="0 0 16 16" aria-hidden="true"><path d="M1 3h14v10H1zm1.5 1.2L8 8.5l5.5-4.3z"/></svg>
        Dkorvand@Harlowtech.com
      </li>
      <li class="address">1180 W 48th St Brookfield Ohio 40112</li>
    </ul>
  </section>

  <section class="card card-back">
    <div class="mark-circle"></div>
    <p class="back-name">HARLOW</p>
    <p class="back-url">www.Harlowtech.com</p>
  </section>
</body>
</html>
```